"Tidewater Sleeve" - Envelope Package for 3 Small Pamphlets/Tracts

We need a design for an envelope package that will be folded to fit 3 small tracts/pamphlets. The final product will be paper that is simply folded - not glued or stapled. The tracts/pamphlets themselves are the ones that can be found at www.briskcanada.ca/literature - they don't need to be designed as we already have them in print. We just want a package/envelope to put them in so we can hand them out in a creative way.

We are looking for a few different ideas to choose from - which is why we are coming to you! Attached is a design brief that outlines the desired format and pictures of mocked-finished product. Also attached is the "G" (Harbourline logo). One of the pictures will provide you with the final product measurement in millimetres. You will have to add safety margins for full bleed to send to the printer. This needs to be designed in Photoshop or Illustrator. Photoshop is preferred.

Although I like the white background because it looks clean, please also provide a darker background to see if the "wallet" effect would work. (I am talking about the outside of the package. the inside should remain white.)

I like the concept of the icons for body and mind, but the icon for "spirit" should be something like a generic sunrise, sunset or peaceful lake.

You will notice that there are "folding" numbers inside the attached mockup picture. We would like them to be nicely designed on the final product so that people know how to fold the envelope, but those numbers should be hidden behind the flaps/pamphlets once the 3 pamphlets are in and the product is fully folded. We would also like to have light grey dotted lines to know where to fold on the inside of the package.

On the centre back panel is where you have the question that states "Know someone who needs healing?"

```html
<!DOCTYPE html>
<html lang="en">
<head>
<meta charset="utf-8">
<title>Tidewater Sleeve – Envelope Package</title>
<link rel="stylesheet" href="https://fonts.googleapis.com/css2?family=Montserrat:wght@200;300;800&display=swap">
<style>
  :root {
    --stage: #9a9899;
    --paper: #ffffff;
    --ink: #4d4d4f;
    --green: #52b948;
    --fold-line: #9b9b9b;
    --fold-mark: #8a8a8a;
    --flap-shade: #ececec;
    --tile-body: #e3a457;
    --tile-mind: #3f63b8;
    --tile-spirit: #5c6f86;
  }
  * { box-sizing: border-box; margin: 0; padding: 0; }
  html, body { width: 1200px; height: 1200px; overflow: hidden; }
  body {
    background: var(--stage);
    font-family: "Montserrat", sans-serif;
    position: relative;
  }

  /* ---------- Outside spread ---------- */
  .outside {
    position: absolute; left: 300px; top: 40px;
    width: 600px; height: 440px;
    display: flex;
    box-shadow: 0 18px 40px rgba(0,0,0,.28);
  }
  .panel {
    position: relative; width: 300px; height: 100%;
    background: var(--paper);
  }
  .panel--back { border-right: 1px solid #e2e2e2; }

  .question {
    position: absolute; top: 70px; left: 0; right: 0;
    text-align: center; font-weight: 800;
    font-size: 38px; line-height: 1.08; letter-spacing: -0.5px;
    color: var(--ink);
  }
  .question .accent { color: var(--green); }

  .brand-band {
    position: absolute; top: 52px; left: 0; width: 185px; height: 56px;
    background: var(--green);
    display: flex; align-items: center; justify-content: flex-end;
    gap: 7px; padding-right: 12px;
  }
  .brand-band .brand-name {
    color: var(--paper); font-weight: 800; font-size: 14px; letter-spacing: 0.5px;
    white-space: nowrap;
  }
  .brand-band .brand-dot {
    width: 10px; height: 10px; border-radius: 50%; background: var(--paper); flex: none;
  }

  .title {
    position: absolute; top: 172px; left: 0; right: 0;
    text-align: center; font-weight: 800;
    font-size: 42px; line-height: 1.04; letter-spacing: -0.5px;
  }
  .title .title-top { color: var(--green); display: block; }
  .title .title-bottom { color: var(--ink); display: block; }

  .tile-row {
    position: absolute; bottom: 40px; left: 0; right: 0;
    display: flex; justify-content: center; gap: 20px;
  }
  .tile {
    width: 70px; height: 70px; border-radius: 10px; display: block;
  }
  .tile--body   { background: var(--tile-body); }
  .tile--mind   { background: var(--tile-mind); }
  .tile--spirit { background: var(--tile-spirit); }

  /* ---------- Inside spread ---------- */
  .inside {
    position: absolute; left: 150px; top: 540px;
    width: 900px; height: 620px;
    background: var(--paper);
    box-shadow: 0 18px 40px rgba(0,0,0,.28);
  }
  .flap-row {
    position: absolute; left: 0; right: 0;
    display: flex;
  }
  .flap-row--top {
    top: 0; height: 78px; border-bottom: 1px solid #6d6d6d;
    background: linear-gradient(180deg, var(--paper) 70%, var(--flap-shade) 100%);
  }
  .flap-row--bottom { bottom: 0; height: 110px; border-top: 1px solid #d0d0d0; }
  .flap {
    flex: 1; display: flex; align-items: center; justify-content: center;
    border-right: 1px solid #cfcfcf;
  }
  .flap:last-child { border-right: none; }
  .flap-label {
    font-weight: 200; font-size: 46px; color: var(--ink); letter-spacing: 1px;
  }
  .pocket-shade {
    position: absolute; left: 0; right: 0; top: 78px; height: 60px;
    background: linear-gradient(180deg, #e4e4e4, rgba(255,255,255,0));
  }

  .fold-line {
    position: absolute; top: 78px; bottom: 110px; width: 0;
    border-left: 1.5px dashed var(--fold-line);
  }
  .fold-line--left { left: 300px; }
  .fold-line--right { left: 600px; }

  .fold-mark {
    position: absolute; display: flex; flex-direction: column; align-items: center;
    color: var(--fold-mark); font-weight: 300; font-size: 15px; gap: 14px;
  }
  .fold-mark--six { left: 282px; top: 270px; }
  .fold-mark--five { left: 598px; top: 228px; }
  .fold-mark svg { width: 22px; height: 14px; }
</style>
</head>
<body>

  <section class="outside" aria-label="Outside of the sleeve">
    <div class="panel panel--back">
      <p class="question">Know<br>someone<br>who<br>needs<br><span class="accent">Healing?</span></p>
      <div class="tile-row">
        <span class="tile tile--body" role="img" aria-label="Photo of a runner at sunrise"></span>
        <span class="tile tile--mind" role="img" aria-label="Illustration of a glowing brain"></span>
        <span class="tile tile--spirit" role="img" aria-label="Photo of a calm lake at sunset"></span>
      </div>
    </div>
    <div class="panel panel--front">
      <div class="brand-band">
        <span class="brand-dot"></span>
        <span class="brand-name">Harbourline</span>
      </div>
      <h1 class="title">
        <span class="title-top">Tidewater</span>
        <span class="title-bottom">Sleeve</span>
      </h1>
      <div class="tile-row">
        <span class="tile tile--body" role="img" aria-label="Photo of a runner at sunrise"></span>
        <span class="tile tile--mind" role="img" aria-label="Illustration of a glowing brain"></span>
        <span class="tile tile--spirit" role="img" aria-label="Photo of a calm lake at sunset"></span>
      </div>
    </div>
  </section>

  <section class="inside" aria-label="Inside of the sleeve">
    <div class="pocket-shade"></div>
    <div class="flap-row flap-row--top">
      <div class="flap"><span class="flap-label">Body</span></div>
      <div class="flap"><span class="flap-label">Mind</span></div>
      <div class="flap"><span class="flap-label">Spirit</span></div>
    </div>

    <div class="fold-line fold-line--left"></div>
    <div class="fold-line fold-line--right"></div>

    <div class="fold-mark fold-mark--six">
      <svg viewBox="0 0 22 14" aria-hidden="true"><path d="M3 12 A8 8 0 0 1 19 12" fill="none" stroke="currentColor" stroke-width="1.4"/><path d="M16 10 L19 13 L21 9" fill="none" stroke="currentColor" stroke-width="1.4"/></svg>
      <span>6</span>
    </div>
    <div class="fold-mark fold-mark--five">
      <svg viewBox="0 0 22 14" aria-hidden="true"><path d="M3 12 A8 8 0 0 1 19 12" fill="none" stroke="currentColor" stroke-width="1.4"/><path d="M1 9 L3 13 L6 10" fill="none" stroke="currentColor" stroke-width="1.4"/></svg>
      <span>5</span>
    </div>

    <div class="flap-row flap-row--bottom">
      <div class="flap"><span class="tile tile--body" role="img" aria-label="Photo of a runner at sunrise"></span></div>
      <div class="flap"><span class="tile tile--mind" role="img" aria-label="Illustration of a glowing brain"></span></div>
      <div class="flap"><span class="tile tile--spirit" role="img" aria-label="Photo of a calm lake at sunset"></span></div>
    </div>
  </section>

</body>
</html>
```